Where the Lantern Fades: A Sacred Wandering

This is a memoir about my breakdown/breakthrough followed by a spiritual awakening in 2012, I found my guru Harsh Omveli Dev, Mother Ayahuasca, and my spiritual mother, Ishu. By 2013, I was headed for a spiritual adventure through India, Southeast India, and Nepal which lasted 14 months. I lived in ashrams, meditated and prayed in temples,, traveled by train and bus, met many enlightened beings and interesting people. During Vipassana, I discovered my true essence- the light of my soul. It is a book of travel, romance, and spiritual growth. My idea is a road lined with temples, etc. I am walking down the road and see myself at the end of the road, facing out, with a bright star in my heart center. I see the colors in muted yellows and other earth-tone hues. Marigolds are used everywhere in the temples to adorn statues and doorways and this speaks to me. The title of the book is about finding out who I am beyond my stories and it is also about how our story will reveal to us who we really are.

Target Market(s)

Spiritual seekers, adventurers, travelers

Industry/Entity Type

Spiritual

Font styles to use
Serif
Sans Serif
Other font styles liked:
• I’m open. I like simplicity

Colors
FFC000
F8CF3A
FAE287
FDF2CF
FEFAEE

Requirements
Must have
• My name: Carla Serena Tovi, Earth tones, pastels, me or a likeness of me, room for ISBN on back cover
Nice to have
• In the photo uploads I drew an idea of what I would like, there is also the idea in the book
Should not have
• I am not a fan of bright colors and that's all I can select here. I like neutral colors, like browns, slate, creams, and whites. This reflects the dusty roads I took throughout my journey.

```html
<!DOCTYPE html>
<html lang="en">
<head>
<meta charset="utf-8">
<title>Where the Lantern Fades — Book Cover</title>
<link rel="stylesheet" href="https://fonts.googleapis.com/css2?family=Gloock&family=Montserrat:wght@500&display=swap">
<style>
  :root {
    --backdrop: #000000;
    --cover-stone: #c5c2bc;
    --art-tan-light: #cdc8be;
    --art-tan-mid: #c9bfab;
    --art-tan-deep: #bfb39b;
    --highlight-sand: #bfb6a5;
    --title-ink: #1f1c1d;
    --author-cream: #f3f1ec;
  }
  * { box-sizing: border-box; margin: 0; padding: 0; }
  html, body {
    width: 1200px;
    height: 1200px;
    overflow: hidden;
    background: var(--backdrop);
  }
  .book-cover {
    position: absolute;
    left: 240px;
    top: 60px;
    width: 720px;
    height: 1080px;
    background: var(--cover-stone);
    overflow: hidden;
  }
  .temple-road-art {
    position: absolute;
    left: 0;
    top: 0;
    width: 720px;
    height: 698px;
    background:
      radial-gradient(ellipse 150px 330px at 50% 40%, var(--art-tan-deep) 0%, rgba(191,179,155,0) 100%),
      radial-gradient(ellipse 130px 220px at 18% 50%, var(--art-tan-mid) 0%, rgba(201,191,171,0) 100%),
      radial-gradient(ellipse 130px 220px at 82% 50%, var(--art-tan-mid) 0%, rgba(201,191,171,0) 100%),
      linear-gradient(180deg, var(--art-tan-light) 0%, var(--art-tan-mid) 70%, var(--art-tan-light) 100%);
  }
  .cover-title {
    position: absolute;
    left: 0;
    right: 0;
    top: 318px;
    text-align: center;
    font-family: "Gloock", "Times New Roman", serif;
    font-weight: 400;
    font-size: 100px;
    line-height: 126px;
    letter-spacing: -0.035em;
    color: var(--title-ink);
  }
  .title-line { display: block; }
  .title-accent {
    position: relative;
    z-index: 0;
  }
  .title-accent::before {
    content: "";
    position: absolute;
    z-index: -1;
    left: -8px;
    right: -200px;
    top: 6px;
    bottom: -6px;
    background: var(--highlight-sand);
  }
  .cover-author {
    position: absolute;
    left: 0;
    right: 0;
    top: 966px;
    text-align: center;
    font-family: "Montserrat", "Helvetica", sans-serif;
    font-weight: 500;
    font-size: 40px;
    letter-spacing: 0.1em;
    color: var(--author-cream);
  }
</style>
</head>
<body>
  <main class="book-cover">
    <div class="temple-road-art" role="img" aria-label="Faint tan line illustration of a stone road lined with temples and seated statues, leading to a temple gateway where the author stands facing out with a glowing star at her heart"></div>
    <h1 class="cover-title">
      <span class="title-line">Where <span class="title-accent">the</span></span>
      <span class="title-line">Lantern</span>
      <span class="title-line">Fades</span>
    </h1>
    <p class="cover-author">Carla Serena Tovi</p>
  </main>
</body>
</html>
```